KLORA product web page

We need a new web design for our KLORA product page. You can find more information about the project on the current web site - www.klora.example

What we need from a new design (uncoded):
- landing pages + template
- all information on one page
- the design should be focused on the product - light bulb + app
- web site should be with some dynamics like a background with parallax effect in the current version
- fonts should be chosen
- a number of illustrations should be designed

Here is schema for a new design: https://files.examplehost.net/d/draw-7QpX2mLk9RtYv4Hs/edit

Here is a document with all texts for a new design: https://files.examplehost.net/d/doc-3WnZ8bJf5KcUe1Ga/edit

Illustrations to use:
v1 - https://files.examplehost.net/f/fold-A1kT9pQw2ZxR
v2 - https://files.examplehost.net/f/fold-B7mH4sLv6YcN

Orbis OS screens: https://files.examplehost.net/f/fold-C3rJ8dKe1WuP

KLORA logo: https://files.examplehost.net/f/fold-D5nF2gTb9XoM
Updates

I forgot to add the definition text "KLORA - is.." to the document with texts. Sorry, my mistake.

Target Market(s)

25-45 year old adults who are interested in "smart" devices for their health.

Industry/Entity Type

Brintel

Colors

Designer to choose colors to be used in the design.

Requirements
Must have
• - landing pages + template
- fonts should be chosen

```html
<!DOCTYPE html>
<html lang="en">
<head>
<meta charset="utf-8">
<title>KLORA App</title>
<link href="https://fonts.googleapis.com/css2?family=Lato:wght@400;700&display=swap" rel="stylesheet">
<style>
  :root {
    --lime: #e0e655;
    --lime-pale: #eff2a8;
    --lime-deep: #cbd047;
    --lime-bright: #d6de2c;
    --olive-text: #8c9230;
    --olive-title: #878c22;
    --ink: #1b1b1b;
    --white: #ffffff;
    --dot-pale: #eef1a6;
    --device-light: #f3f3f1;
    --device-shade: #e2e2df;
  }
  * { margin: 0; padding: 0; box-sizing: border-box; }
  html, body { width: 1200px; height: 1000px; overflow: hidden; }
  body {
    position: relative;
    background: var(--lime);
    font-family: "Lato", sans-serif;
  }
  .top-band {
    position: absolute; left: 0; top: 0; width: 1200px; height: 120px;
    background: var(--lime-pale);
  }
  .header-bar {
    position: absolute; left: 0; top: 30px; width: 1200px; height: 60px;
    background: var(--white);
  }
  .brand-badge {
    position: absolute; left: 141px; top: 20px; width: 80px; height: 80px;
    border-radius: 50%; background: var(--lime-bright);
    display: flex; align-items: center; justify-content: center;
    color: var(--white); font-weight: 700; font-size: 15px; letter-spacing: 1px;
  }
  .main-nav {
    position: absolute; top: 47px; right: 141px;
    display: flex; gap: 53px;
    font-size: 22px; letter-spacing: 4.4px; color: var(--ink);
    line-height: 28px;
  }
  .main-nav .is-active { color: var(--lime-bright); font-weight: 700; }
  .section-dots {
    position: absolute; left: 20px; top: 459px;
    display: flex; flex-direction: column; gap: 15px;
  }
  .section-dots span {
    width: 15px; height: 15px; border-radius: 50%; background: var(--dot-pale);
  }
  .section-dots .is-current { background: var(--white); }
  .app-intro {
    position: absolute; left: 131px; top: 364px; width: 455px;
    color: var(--olive-text); font-size: 16px; line-height: 25px;
  }
  .app-intro h1 {
    font-size: 25px; letter-spacing: 3px; font-weight: 700;
    color: var(--olive-title); margin-bottom: 31px; line-height: 30px;
  }
  .app-intro p { margin-bottom: 25px; }
  .app-intro strong { font-weight: 700; }
  .device {
    position: absolute;
    background: linear-gradient(160deg, var(--device-light) 0%, var(--device-shade) 100%);
    box-shadow: 0 8px 24px rgba(150, 155, 40, 0.25);
  }
  .device-large { left: 667px; top: 304px; width: 225px; height: 439px; border-radius: 40px; }
  .device-small { left: 902px; top: 353px; width: 178px; height: 385px; border-radius: 22px; }
  .site-footer {
    position: absolute; left: 0; top: 961px; width: 1200px; height: 39px;
    background: var(--lime-deep); color: var(--dot-pale);
  }
  .footer-link {
    position: absolute; left: 141px; top: 11px;
    font-size: 14px; font-weight: 700; letter-spacing: 0.5px;
  }
  .footer-copy {
    position: absolute; right: 148px; top: 9px;
    display: flex; align-items: center; gap: 10px;
    font-size: 11px;
  }
  .footer-copy .footer-brand { font-size: 18px; font-weight: 700; letter-spacing: 1px; }
</style>
</head>
<body>
  <div class="top-band"></div>
  <header class="header-bar"></header>
  <div class="brand-badge">KLORA</div>
  <nav class="main-nav">
    <span class="is-active">PRE-ORDER</span>
    <span>BLOG</span>
    <span>CONTACTS</span>
    <span>RU</span>
  </nav>

  <div class="section-dots">
    <span></span><span class="is-current"></span><span></span><span></span><span></span><span></span>
  </div>

  <section class="app-intro">
    <h1>KLORA APP</h1>
    <p>KLORA Application allows you to control each lightbulb at home. Manage your lighting by creating functional groups and adding/excluding lightbulbs. Correctly matched lighting will help you work more productively and relax to the outmost.</p>
    <p>Create light scenes and adapt them to your needs. KLORA App memorizes your favorite moods, so that you can use your settings anytime.</p>
    <p><strong>Play with million colors and adjust the brightness of your home lighting</strong>. KLORA works on Orbis OS 6+ and Droidline 4+.</p>
  </section>

  <div class="device device-large" role="img" aria-label="Large white smartphone showing the KLORA app start screen"></div>
  <div class="device device-small" role="img" aria-label="Small white smartphone showing the KLORA app start screen"></div>

  <footer class="site-footer">
    <span class="footer-link">CONTACTS</span>
    <span class="footer-copy">COPYRIGHT © <span class="footer-brand">KLORA</span></span>
  </footer>
</body>
</html>
```